Redesign Comparisson chart - make modern and effective

Use your imaginations to make a powerful distinction between KMV & other holistic modalities. There are 7 elements physical, mental, emotional, energetic, subconscious, superconscious and before and after testing.
We want it to be obvious that KMV is the only modality that works on all these elements simultaneously. We do not want to include any chakras as we want this information to be accepted by a wide range of people and belief systems.'

We want it to look simple but effective. Professional but powerful. We want KMV to stand out even of you eye just passed over i.
Updates

Hi everyone, thanks for your submissions so far. Basically what this image is meant to represent is a comparison chart between all the modalities There are 5 elements physical, mental, emotional, subconscious and superconscious. we want to reflect that KMV is the only modality that works on all these elements simultaneously. As we want the concept to be accepted and not considered woo woo, we want to steer away from chakras.

Target Market(s)

Professionals

Industry/Entity Type

Professional services

Font styles to use
Sans Serif
Other font styles liked:
• Poppins Monserratt

Colors
0094D4
00A9DD
6FCCEA
C7EBF8
E9F6FB

Requirements
Must have
• Clear/professional and clean look. Brand colours and logos. All typography and formats must be cohesive.
Nice to have
• More easy to read, different layout
Should not have
• Do not change the data just the way its presented. No chakras

```html
<!DOCTYPE html>
<html lang="en">
<head>
<meta charset="utf-8">
<title>KMV Method – Modality Comparison</title>
<link href="https://fonts.googleapis.com/css2?family=Poppins:wght@400;500;600;700&display=swap" rel="stylesheet">
<style>
:root{
  --phys:#e04a3f;--ment:#63bfdf;--emo:#5aae45;--ener:#f7991f;--sub:#ecd02b;--super:#7d69ad;--test:#d872a9;
  --brand:#2fb4e6;--title:#5cc2ec;--band:#c9ecf9;--panel:#e8f6fb;--label:#b8ddf3;--line:#9fcde8;--ink:#1c2733;
}
*{margin:0;padding:0;box-sizing:border-box}
html,body{width:1200px;height:1046px;overflow:hidden;background:#fff}
body{font-family:"Poppins",sans-serif;color:var(--ink);position:relative}
.brand{position:absolute;left:83px;top:20px;display:flex;align-items:center;gap:10px}
.brand-dot{width:62px;height:62px;border-radius:50%;background:var(--brand)}
.brand-name{font-weight:700;font-size:30px;color:var(--brand);letter-spacing:.5px}
.headline{position:absolute;left:280px;width:886px;top:22px;text-align:center}
.headline h1{font-size:20px;font-weight:700;color:var(--title);letter-spacing:.2px;line-height:26px}
.headline p{font-size:11px;font-weight:600;line-height:17.5px;margin-top:3px}
.band{position:absolute;left:0;top:97px;width:1200px;height:763px;background:var(--band)}
.panel{position:absolute;left:291px;top:120px;width:820px;height:711px;background:var(--panel);border-radius:14px 14px 0 0}
.col-heads{position:absolute;left:291px;top:131px;display:grid;grid-template-columns:109px 111px 109px 111px 118px 120px 119px;height:34px}
.col-heads span{display:flex;align-items:center;justify-content:center;text-align:center;font-weight:600;font-size:15px;line-height:15px;border-left:1px solid var(--line)}
.col-heads span:first-child{border-left:0}
.col-heads .small{font-size:12.5px}
.feature{position:absolute;left:58px;top:165px;width:1092px;height:51px;background:#fff;border-radius:9px;box-shadow:0 3px 8px rgba(60,110,150,.25);
  display:grid;grid-template-columns:233px 109px 111px 109px 111px 118px 120px 119px 62px}
.feature > div{border-left:1px solid #7fb7d8;display:flex;align-items:center;justify-content:center}
.feature > div:first-child,.feature > div:last-child{border-left:0}
.feature .who{justify-content:flex-start;padding-left:56px;gap:10px;font-size:11.5px;font-weight:500;line-height:14px}
.who-dot{width:36px;height:36px;border-radius:50%;background:var(--brand);flex:none}
.table{position:absolute;left:93px;top:216px;width:995px}
.row{display:grid;grid-template-columns:198px 109px 111px 109px 111px 118px 120px 119px}
.row > *{display:flex;align-items:center;justify-content:center;border-bottom:1px solid var(--line);border-left:1px solid var(--line)}
.row .lbl{background:var(--label);justify-content:flex-start;padding-left:14px;font-size:12.5px;font-weight:500;line-height:14.5px;border-left:0;border-bottom-color:#e3f3fb}
.row:last-child > *{border-bottom:0}
.row:last-child > i{border-bottom:0}
.d{display:block;width:13px;height:13px;transform:rotate(45deg)}
.d.big{width:19px;height:19px}
.phys{background:var(--phys)}.ment{background:var(--ment)}.emo{background:var(--emo)}.ener{background:var(--ener)}.sub{background:var(--sub)}.super{background:var(--super)}.test{background:var(--test)}
.c-phys{color:var(--phys)}.c-ment{color:var(--ment)}.c-emo{color:var(--emo)}.c-ener{color:var(--ener)}.c-sub{color:var(--sub)}.c-super{color:var(--super)}.c-test{color:var(--test)}
.legend{position:absolute;top:874px}
.legend h3{display:flex;align-items:center;gap:10px;font-size:14px;font-weight:600;line-height:18px;margin-bottom:2px}
.legend h3 .d{width:9px;height:9px;margin-left:2px}
.legend p{font-size:11.6px;line-height:13.4px;text-align:justify}
.legend .gap{margin-top:8px}
.footer-brand{position:absolute;left:99px;top:1013px;display:flex;align-items:center;gap:8px;font-size:9.5px;color:var(--brand)}
.footer-brand .mark{width:16px;height:16px;border-radius:50%;background:var(--brand)}
.footer-brand strong{font-size:14px;font-weight:700}
.footer-brand .sep{width:1px;height:16px;background:var(--brand)}
</style>
</head>
<body>
<header>
  <div class="brand"><span class="brand-dot"></span><span class="brand-name">KMV</span></div>
  <div class="headline">
    <h1>CHOOSE KMV FOR FAST, IMMEDIATE AND POWERFUL RESULTS</h1>
    <p>I MUST EXPERIENCE HEALING ON ALL LEVELS, I AM NOT JUST A BODY. I WANT TO LEARN HOW TO HEAL MYSELF, SO I’M NOT DEPENDENT ON OTHERS.<br>I WANT TO RELEASE ALL MY EMOTIONAL AND MENTAL BLOCKS, SO I CAN BE THE BEST VERSION OF MYSELF.</p>
  </div>
</header>

<div class="band"></div>
<div class="panel"></div>

<div class="col-heads">
  <span class="c-phys">PHYSICAL</span>
  <span class="c-ment">MENTAL</span>
  <span class="c-emo">EMOTIONAL</span>
  <span class="c-ener">ENERGETIC</span>
  <span class="c-sub small">SUBCONSCIOUS</span>
  <span class="c-super small">SUPERCONSCIOUS</span>
  <span class="c-test small">BEFORE &amp;<br>AFTER TESTING</span>
</div>

<div class="feature">
  <div class="who"><span class="who-dot"></span><span>KMV<br>METHOD</span></div>
  <div><b class="d big phys"></b></div>
  <div><b class="d big ment"></b></div>
  <div><b class="d big emo"></b></div>
  <div><b class="d big ener"></b></div>
  <div><b class="d big sub"></b></div>
  <div><b class="d big super"></b></div>
  <div><b class="d big test"></b></div>
  <div></div>
</div>

<div class="table">
  <div class="row" style="height:82px"><span class="lbl">• MASSAGE<br>• YOGA<br>• NATROPATHY<br>• AYURVEDIC MEDICINE<br>• WESTERN MEDICINE</span><i><b class="d phys"></b></i><i></i><i></i><i></i><i></i><i></i><i></i></div>
  <div class="row" style="height:29px"><span class="lbl">• PSYCHIC INTUITIVE</span><i><b class="d phys"></b></i><i><b class="d ment"></b></i><i></i><i></i><i></i><i></i><i></i></div>
  <div class="row" style="height:29px"><span class="lbl">• FAMILY CONSTELLATION</span><i><b class="d phys"></b></i><i><b class="d ment"></b></i><i></i><i><b class="d ener"></b></i><i></i><i></i><i></i></div>
  <div class="row" style="height:32px"><span class="lbl">• ACUPUNCTURE</span><i><b class="d phys"></b></i><i></i><i></i><i><b class="d ener"></b></i><i></i><i></i><i></i></div>
  <div class="row" style="height:32px"><span class="lbl">• NUTRITIONAL HEALING</span><i><b class="d phys"></b></i><i></i><i></i><i></i><i></i><i></i><i><b class="d test"></b></i></div>
  <div class="row" style="height:31px"><span class="lbl">• CHINESE MEDICINE</span><i><b class="d phys"></b></i><i></i><i></i><i><b class="d ener"></b></i><i></i><i></i><i><b class="d test"></b></i></div>
  <div class="row" style="height:42px"><span class="lbl">• KINESIOLOGY<br>• BOWEN THERAPY</span><i><b class="d phys"></b></i><i></i><i></i><i></i><i><b class="d sub"></b></i><i></i><i><b class="d test"></b></i></div>
  <div class="row" style="height:32px"><span class="lbl">• EFT</span><i><b class="d phys"></b></i><i><b class="d ment"></b></i><i></i><i></i><i><b class="d sub"></b></i><i></i><i><b class="d test"></b></i></div>
  <div class="row" style="height:31px"><span class="lbl">• CHIROPRACTIC</span><i><b class="d phys"></b></i><i></i><i></i><i><b class="d ener"></b></i><i><b class="d sub"></b></i><i></i><i><b class="d test"></b></i></div>
  <div class="row" style="height:42px"><span class="lbl">• REIKI<br>• CRYSTAL HEALING</span><i></i><i></i><i></i><i><b class="d ener"></b></i><i></i><i></i><i></i></div>
  <div class="row" style="height:32px"><span class="lbl">• ENERGY MEDICINE</span><i></i><i></i><i></i><i><b class="d ener"></b></i><i></i><i></i><i><b class="d test"></b></i></div>
  <div class="row" style="height:32px"><span class="lbl">• THETA HEALING</span><i></i><i></i><i></i><i></i><i><b class="d sub"></b></i><i><b class="d super"></b></i><i></i></div>
  <div class="row" style="height:31px"><span class="lbl">• PSYCHOLOGY</span><i></i><i><b class="d ment"></b></i><i></i><i></i><i></i><i></i><i></i></div>
  <div class="row" style="height:43px"><span class="lbl">• MINDFULNESS MEDITATION<br>• LIFE COACHING</span><i></i><i><b class="d ment"></b></i><i></i><i></i><i></i><i></i><i><b class="d test"></b></i></div>
  <div class="row" style="height:42px"><span class="lbl">• HYPNOTHERAPY<br>• INNER CHILD HEALING</span><i></i><i><b class="d ment"></b></i><i></i><i></i><i><b class="d sub"></b></i><i></i><i></i></div>
  <div class="row" style="height:53px"><span class="lbl">• NLP<br>• TIMELINE THERAPY</span><i></i><i><b class="d ment"></b></i><i></i><i></i><i><b class="d sub"></b></i><i></i><i><b class="d test"></b></i></div>
</div>

<section class="legend" style="left:93px;width:220px">
  <h3 class="c-phys"><b class="d phys"></b>PHYSICAL</h3>
  <p>Most modalities, including, a western medicine, focus on and treat the physical body only. The KMV process enables you to engage in healing your own body during the session. There is no muscle testing, no hands-on healing and no herbal remedies or medicines.</p>
</section>
<section class="legend" style="left:340px;width:218px">
  <h3 class="c-ment"><b class="d ment"></b>MENTAL</h3>
  <p>KMV enables you to use your own consciousness to self-heal. We don’t give you advice or coaching, we allow your mind to heal itself.</p>
  <h3 class="c-ener gap"><b class="d ener"></b>ENERGETIC</h3>
  <p>Most modalities try to move the energy in your body for you. KMV enables and empowers you to do it yourself.</p>
</section>
<section class="legend" style="left:584px;width:268px">
  <h3 class="c-emo"><b class="d emo"></b>EMOTIONAL</h3>
  <p>KMV is the only modality that engages your emotions on a physical level. Emotions get stuck in your body and can cause illness over time if left unchecked. KMV enables you to experience fast and powerful emotional releasing</p>
  <h3 class="c-super gap"><b class="d super"></b>SUPERCONSCIOUS</h3>
  <p>KMV is the only modality that enables you to access and heal your superconscious mind yourself.</p>
</section>
<section class="legend" style="left:877px;width:234px">
  <h3 class="c-sub"><b class="d sub"></b>SUBCONSCIOUS</h3>
  <p>Some modalities, like Kinesiology, access your subconscious through muscle testing. KMV empowers you to access your own subconscious and heal it yourself.</p>
  <h3 class="c-test gap"><b class="d test"></b>BEFORE &amp; AFTER TESTING</h3>
  <p>KMV is the only modality that enables you to provide before and after results, which are documented by us, and analysed by you with our help.</p>
</section>

<div class="footer-brand"><span class="mark"></span><strong>Brightwell</strong><span class="sep"></span><span>www.brightwell.com.au</span></div>
</body>
</html>
```